Brookvale Estates LLC stationary for a real estate property management company.

Create stationary (letterhead, envelopes, business cards) using Brookvale Estates LLC logo as primary creative element. Stationary design needs to be horizontal, leaving as much space as possible for correspondence copy. See attached Creative Brief and past stationary files for details.

Target Market(s)

Prospective apartment residents and current residents, vendors, and government agencies.

Industry/Entity Type

Property Management

Contact Information for Business Card

Business card employee title: Property Manager. Should include address, phone, fax, email, website, slogan, and Brookvale Estates logo.

Font styles to use
Sans Serif

Colors
0592cd
000000

Requirements
Must have
• Tone should be conservative, institutional, business (i.e. banking, finance, real estate). Must include: address, phone, fax, website, and slogan (see attached Creative Brief). Should be a horizontal design, leaving as much room as possible for letter correspondence copy.
Nice to have
• Please use an Arial or Helvetica style font.
Should not have
• Letterhead layout should leave as much room as possible for copy.

```html
<!DOCTYPE html>
<html lang="en">
<head>
<meta charset="utf-8">
<title>Brookvale Estates LLC – Stationery</title>
<link rel="stylesheet" href="https://fonts.googleapis.com/css2?family=Arimo:wght@400;700&family=Open+Sans:wght@400&display=swap">
<style>
  :root {
    --brand-blue: #0b6aa8;
    --charcoal: #404143;
    --ink: #333333;
    --paper: #ffffff;
    --paper-soft: #f4f4f4;
    --backdrop: #dcdcdc;
    --rule: #c9c9c9;
  }
  * { margin: 0; padding: 0; box-sizing: border-box; }
  html, body { width: 1200px; height: 754px; overflow: hidden; }
  body {
    position: relative;
    background: var(--backdrop);
    font-family: "Arimo", Arial, sans-serif;
    color: var(--ink);
  }
  .sheet { position: absolute; box-shadow: 0 2px 6px rgba(0,0,0,.25); }

  .brand { display: flex; align-items: center; gap: 6px; }
  .brand-square { background: var(--brand-blue); flex: none; }
  .brand-name {
    font-family: "Arimo", Arial, sans-serif;
    font-weight: 700;
    color: var(--brand-blue);
    line-height: 1.05;
    text-transform: uppercase;
  }
  .brand--light .brand-name { color: #ffffff; }

  .contact-list { list-style: none; }
  .contact-list li { display: flex; align-items: center; gap: 4px; }
  .contact-list svg { flex: none; fill: var(--brand-blue); }

  /* Letterhead */
  .letterhead { left: 36px; top: 32px; width: 488px; height: 688px; background: var(--paper); }
  .letterhead .brand { position: absolute; left: 46px; top: 55px; }
  .letterhead .brand-square { width: 26px; height: 26px; }
  .letterhead .brand-name { font-size: 13px; }
  .letterhead-contact {
    position: absolute; left: 316px; top: 44px; height: 66px;
    border-left: 1px solid var(--rule); padding-left: 10px;
    font-size: 7.4px; line-height: 9.6px; color: #444;
  }
  .letterhead-contact address { font-style: normal; margin-bottom: 2px; }
  .letter-body {
    position: absolute; left: 49px; top: 192px; width: 394px;
    font-family: "Open Sans", Arial, sans-serif; color: #444;
  }
  .letter-body p { font-size: 6.9px; line-height: 11.8px; margin-bottom: 11.8px; }
  .letter-body .letter-salutation { font-size: 13px; line-height: 18px; margin-bottom: 26px; }
  .letter-body .letter-closing { margin-top: 22px; margin-bottom: 4px; }
  .signature { display: block; width: 64px; height: 26px; background: #e2e2e2; }

  /* Business card front */
  .card-front { left: 578px; top: 74px; width: 266px; height: 152px; background: #f2f2f2; padding: 14px 15px; }
  .card-front .brand-square { width: 18px; height: 18px; }
  .card-front .brand-name { font-size: 10.5px; }
  .card-person { margin-top: 9px; font-size: 9.5px; font-weight: 700; color: var(--brand-blue); }
  .card-title { font-size: 6.6px; color: #444; margin-bottom: 5px; }
  .card-front address { font-style: normal; font-size: 5.8px; line-height: 8px; color: #444; margin-bottom: 4px; }
  .card-front .contact-list { font-size: 5.8px; line-height: 8.4px; color: #444; }
  .card-slogan { margin-top: 4px; font-size: 6.2px; font-weight: 700; color: var(--brand-blue); }

  /* Business card back */
  .card-back { left: 877px; top: 144px; width: 267px; height: 152px; background: var(--charcoal);
    display: flex; align-items: center; justify-content: center; }
  .card-back .brand-square { width: 24px; height: 24px; }
  .card-back .brand-name { font-size: 13px; }

  /* Envelope back */
  .envelope-back { left: 615px; top: 350px; width: 548px; height: 248px; background: var(--paper-soft); }
  .envelope-flap { position: absolute; left: 0; top: 0; }
  .envelope-back .brand { position: absolute; left: 219px; top: 30px; }
  .envelope-back .brand-square { width: 18px; height: 18px; }
  .envelope-back .brand-name { font-size: 10px; }

  /* Envelope front */
  .envelope-front { left: 547px; top: 471px; width: 550px; height: 249px; background: var(--paper-soft); }
  .envelope-front .brand { position: absolute; left: 23px; top: 24px; }
  .envelope-front .brand-square { width: 22px; height: 22px; }
  .envelope-front .brand-name { font-size: 11.5px; }
  .envelope-front address {
    position: absolute; left: 38px; top: 67px;
    font-style: normal; font-size: 7.4px; line-height: 9.4px; color: #444;
  }
</style>
</head>
<body>

<section class="sheet letterhead" aria-label="Letterhead">
  <div class="brand">
    <span class="brand-square"></span>
    <span class="brand-name">Brookvale<br>Estates LLC</span>
  </div>
  <div class="letterhead-contact">
    <address>2750 Alder Ridge Road #B210<br>Fairview, CA 90210</address>
    <ul class="contact-list">
      <li><svg width="7" height="7" viewBox="0 0 10 10"><path d="M2 0h2l1 3-1.5 1a6 6 0 0 0 2.5 2.5L7 5l3 1v2c0 1-1 2-2 2C4 10 0 6 0 2 0 1 1 0 2 0z"/></svg>555-410-2280</li>
      <li><svg width="8" height="7" viewBox="0 0 12 10"><rect x="3" y="0" width="6" height="3"/><rect x="0" y="3.5" width="12" height="4.5" rx="1"/><rect x="3" y="7" width="6" height="3"/></svg>555-410-2281</li>
      <li><svg width="8" height="6" viewBox="0 0 12 9"><rect width="12" height="9"/><path d="M0 0l6 5 6-5" stroke="#fff" fill="none"/></svg>daniel@brookvaleestates.us</li>
      <li><svg width="7" height="7" viewBox="0 0 10 10"><circle cx="5" cy="5" r="5"/><path d="M0 5h10M5 0c-3 3-3 7 0 10M5 0c3 3 3 7 0 10" stroke="#fff" stroke-width=".8" fill="none"/></svg>www.brookvaleestates.us</li>
    </ul>
  </div>
  <div class="letter-body">
    <p class="letter-salutation">Dear Mr. Carter,</p>
    <p>Lorem ipsum dolor sit amet, consectetur adipiscing elit. Donec orci purus, luctus vitae dignissim eu, iaculis sed purus. Vivamus faucibus, ipsum nec aliquet viverra, leo mauris condimentum ligula, sit amet sagittis enim ligula quis arcu. Nam egestas tortor id nisi porttitor mattis. In tortor ante, ultricies in suscipit a, tempus non massa. Vivamus et auctor mi. Fusce vel massa nulla. Phasellus nec eros mauris, et scelerisque orci.</p>
    <p>Donec malesuada orci vitae nulla accumsan porta a id massa. Quisque accumsan iaculis magna sit amet fringilla. Maecenas consequat, magna eget tincidunt semper, odio nibh rutrum mi, id feugiat ante nisi eu risus. Vestibulum nunc orci, rhoncus a placerat in, ultricies in mi. Cras mattis varius eros, vel fringilla nisi suscipit eget. Quisque scelerisque sagittis nulla at porttitor.</p>
    <p>Sed id augue vitae urna euismod commodo aliquet a quam. Pellentesque arcu velit, cursus et malesuada ut, consequat et diam. Nullam erat sem, rhoncus id ullamcorper vitae, rhoncus et arcu. In ultricies ultricies nulla, ut rutrum nisi iaculis at. Donec eu magna a metus ornare faucibus. Fusce aliquet faucibus ultricies. Morbi semper, est id tincidunt gravida, sem arcu adipiscing lacus, ac bibendum nulla leo eu purus. Quisque nec diam sed risus consectetur a accumsan quis quis nibh. Vestibulum id purus lorem.</p>
    <p>It is a long established fact that a reader will be distracted by the readable content of a page when looking at its layout. The point of using Lorem Ipsum is that it has a more-or-less normal distribution of letters, as opposed to using ‘Content here, content here’, making it look like readable English. Many desktop publishing packages</p>
    <p class="letter-closing">Sincerely,</p>
    <span class="signature" role="img" aria-label="Handwritten signature"></span>
  </div>
</section>

<section class="sheet card-front" aria-label="Business card front">
  <div class="brand">
    <span class="brand-square"></span>
    <span class="brand-name">Brookvale<br>Estates LLC</span>
  </div>
  <p class="card-person">DANIEL HARPER</p>
  <p class="card-title">Property Manager</p>
  <address>2750 Alder Ridge Road #B210<br>Fairview, CA 90210</address>
  <ul class="contact-list">
    <li><svg width="5" height="5" viewBox="0 0 10 10"><path d="M2 0h2l1 3-1.5 1a6 6 0 0 0 2.5 2.5L7 5l3 1v2c0 1-1 2-2 2C4 10 0 6 0 2 0 1 1 0 2 0z"/></svg>555-410-2280</li>
    <li><svg width="6" height="5" viewBox="0 0 12 10"><rect x="3" y="0" width="6" height="3"/><rect x="0" y="3.5" width="12" height="4.5" rx="1"/><rect x="3" y="7" width="6" height="3"/></svg>555-410-2281</li>
    <li><svg width="6" height="5" viewBox="0 0 12 9"><rect width="12" height="9"/><path d="M0 0l6 5 6-5" stroke="#fff" fill="none"/></svg>daniel@brookvaleestates.us</li>
    <li><svg width="5" height="5" viewBox="0 0 10 10"><circle cx="5" cy="5" r="5"/></svg>www.brookvaleestates.us</li>
  </ul>
  <p class="card-slogan">Multifamily Property Management</p>
</section>

<section class="sheet card-back" aria-label="Business card back">
  <div class="brand brand--light">
    <span class="brand-square"></span>
    <span class="brand-name">Brookvale<br>Estates LLC</span>
  </div>
</section>

<section class="sheet envelope-back" aria-label="Envelope back">
  <svg class="envelope-flap" width="548" height="96" viewBox="0 0 548 96">
    <path d="M0 0H548V12Q540 80 500 90Q490 93 470 93H78Q58 93 48 90Q8 80 0 12Z" fill="var(--charcoal)"/>
  </svg>
  <div class="brand brand--light">
    <span class="brand-square"></span>
    <span class="brand-name">Brookvale<br>Estates LLC</span>
  </div>
</section>

<section class="sheet envelope-front" aria-label="Envelope front">
  <div class="brand">
    <span class="brand-square"></span>
    <span class="brand-name">Brookvale<br>Estates LLC</span>
  </div>
  <address>2750 Alder Ridge Road #B210<br>Fairview, CA 90210</address>
</section>

</body>
</html>
```